Design for a real estate wev portal

Contents and features of the site
---------------------------------
Website in 5 languages: French, Dutch, English, German, Spanish.
English name of the site: Harbor Nest Place
Main purpose of the site:
- allow people to rent their house/ appartment for flatsharing purposes.
- help people wanting to find a room in flatsharing
- help people to find additional roommates for their flatsharing
Key interaction sequence:
1. I create a "group" of people who have common interest/hobbies
2. People who have the same interests/hobbies join my group
3. I look for a house/appartment to host my group
Website structure will be the following:
- Home
- Groups
-- Look for a group
--- Join a group
-- Create a group
- Properties
-- Look for a house/appartement
-- Apply
- Sales conditions
- Contact
- My account
-- My profile
-- My groups OR my properties
Your mission
------------
The client has no graphical guidelines, simply a logo (see attached).
We need a (responsive compliant) design for the following pages (we expect PSD's from you. No HTML nor CSS):
1. homepage (see example and wireframe attached)
2. properties search result list (see wireframe attached)
3. "detailed" form for properties
4. groups search result list
5. "detailed" form for groups
6. my account page
FOR THE COMPETITION step we only expect from you the design of first 2 screens.
Based on that, we will select the designer who will win the project, and will have to design the 4 remaining screens.
Target Market(s)
B2C
Industry/Entity Type
Real Estate
Number of Pages Required
5+ page
Look and feel
Each slider illustrates characteristics of the customer's brand and the style your logo design should communicate.

```html
<!DOCTYPE html>
<html lang="en">
<head>
<meta charset="utf-8">
<title>Harbor Nest Place</title>
<link href="https://fonts.googleapis.com/css2?family=Montserrat:wght@400;600;700&family=Open+Sans:wght@400;600&display=swap" rel="stylesheet">
<style>
:root{
  --green:#6abf45;
  --green-dark:#3f6b2f;
  --teal:#1aa6b7;
  --teal-head:#1897ad;
  --text:#555;
  --heading:#4a4a4a;
  --bar:#eeeeee;
  --line:#e6e6e6;
  --card:#f5f5f5;
  --white:#fff;
}
*{box-sizing:border-box;margin:0;padding:0}
html,body{width:1200px;height:2719px;overflow:hidden}
body{position:relative;background:var(--white);font-family:"Open Sans",Arial,sans-serif;color:var(--text)}
.abs{position:absolute}

/* top bar */
.topbar{left:0;top:0;width:1200px;height:47px;background:var(--bar)}
.search{left:199px;top:12px;width:221px;height:26px;background:#fff;border:1px solid #ddd;border-radius:2px;font-size:10px;color:#aaa;padding:6px 9px}
.search svg{position:absolute;right:8px;top:7px}
.langs{right:190px;top:17px;font-family:"Montserrat",sans-serif;font-size:11px;font-weight:600;color:#333;letter-spacing:.2px}
.langs .on{color:var(--green)}

/* header */
.nav-link{top:97px;font-family:"Montserrat",sans-serif;font-size:10px;color:#444;white-space:nowrap}
.nav-link.on{color:var(--green)}
.brand{display:flex;align-items:center;justify-content:center;gap:7px;font-family:"Montserrat",sans-serif;font-weight:700;font-size:15px;color:#3a3a3a;white-space:nowrap}
.brand i{width:9px;height:9px;border-radius:50%;background:var(--green);display:block;flex:none}
.brand.head{left:510px;top:92px;width:180px}
.account{right:194px;top:96px;font-family:"Montserrat",sans-serif;font-size:10px;color:#444;display:flex;align-items:center;gap:8px;white-space:nowrap}

/* hero */
.hero{left:0;top:169px;width:1200px;height:534px;background:linear-gradient(90deg,#4e7a3a 0%,#cdd3d4 18%,#e9ecee 45%,#eef0f2 60%,#cfd6d8 82%,#4f7b3b 100%)}
.panel{top:248px;width:401px;height:374px;border-radius:4px;box-shadow:0 3px 8px rgba(0,0,0,.25);color:#fff}
.panel.rent{left:190px;background:rgba(106,191,69,.96)}
.panel.owner{left:609px;background:rgba(26,166,183,.93)}
.panel h2{position:absolute;left:0;right:0;top:62px;text-align:center;font-family:"Montserrat",sans-serif;font-size:16px;font-weight:700;letter-spacing:.3px}
.tile{position:absolute;top:111px;width:187px;height:131px;border:2px solid #fff;border-radius:4px;background:rgba(255,255,255,.08)}
.tile svg{position:absolute;left:51px;top:23px;width:80px;height:80px}
.tile-label{position:absolute;top:262px;width:187px;text-align:center;font-family:"Montserrat",sans-serif;font-weight:700;font-size:17px;line-height:23px}

/* spotlight */
.sec-title{font-family:"Montserrat",sans-serif;font-weight:700;font-size:18px;color:var(--heading);text-align:center;width:390px}
.card{width:390px;height:175px;background:var(--card)}
.card .photo{position:absolute;left:0;top:0;width:183px;height:175px}
.card .body{position:absolute;left:206px;top:18px;width:170px;font-size:10px;line-height:16px;color:#666}
.card h3{font-family:"Montserrat",sans-serif;font-size:12.5px;font-weight:700;color:var(--green);margin-bottom:12px}
.btn{height:41px;border-radius:4px;background:var(--green);color:#fff;font-family:"Montserrat",sans-serif;font-weight:700;font-size:10px;display:flex;align-items:center;justify-content:center;box-shadow:0 2px 3px rgba(0,0,0,.2)}

/* selling points */
.band{left:0;top:1332px;width:1200px;height:357px;background:#f7f7f7}
.sp-title{width:390px;text-align:center;font-family:"Montserrat",sans-serif;font-weight:700;font-size:22px;line-height:26px;color:var(--teal-head)}
.sp-box{width:390px;height:187px;background:#fff;border:1px solid var(--line);border-radius:4px;padding:30px 24px;font-size:10.5px;line-height:18px;text-align:center;color:#666}

/* faq */
.faq-title{left:300px;top:1768px;width:600px;text-align:center;font-family:"Montserrat",sans-serif;font-weight:700;font-size:22px;line-height:28px;color:var(--teal-head)}
.faq{left:201px;width:798px;border:1px solid var(--line);background:#fff;box-shadow:0 1px 3px rgba(0,0,0,.08)}
.faq.active{background:var(--green);border-color:var(--green);color:#fff}
.faq .num{position:absolute;left:20px;top:42px;font-family:"Montserrat",sans-serif;font-weight:700;font-size:82px;line-height:70px;color:var(--green)}
.faq.active .num{color:#fff}
.faq p{position:absolute;left:109px;top:40px;width:680px;font-size:10.5px;line-height:19px}
.faq .more{position:absolute;right:4px;bottom:6px;width:80px;height:30px;background:var(--green-dark);color:#fff;font-family:"Montserrat",sans-serif;font-weight:700;font-size:12px;display:flex;align-items:center;justify-content:center}
.btn-teal{left:812px;top:2358px;width:187px;height:44px;border-radius:5px;background:var(--teal);color:#fff;font-family:"Montserrat",sans-serif;font-weight:700;font-size:12px;display:flex;align-items:center;justify-content:center}

.block{top:2442px;width:390px;height:121px;border-radius:4px;display:flex;align-items:center;justify-content:center;font-family:"Montserrat",sans-serif;font-weight:700;font-size:16.5px;box-shadow:0 2px 3px rgba(0,0,0,.2)}
.block.green{left:201px;background:var(--green);color:#fff}
.block.grey{left:611px;background:#eeeeee;color:#666}

/* footer */
.footer{left:0;top:2607px;width:1200px;height:112px;background:#f4f4f4}
.footer .brand{position:absolute;left:201px;top:44px}
.copy{right:201px;top:49px;font-family:"Montserrat",sans-serif;font-size:13px;font-weight:600;color:#666;letter-spacing:.3px}
</style>
</head>
<body>

<div class="abs topbar"></div>
<div class="abs search">Search
  <svg width="12" height="12" viewBox="0 0 12 12"><circle cx="5" cy="5" r="3.6" fill="none" stroke="#6abf45" stroke-width="1.6"/><line x1="7.6" y1="7.6" x2="11" y2="11" stroke="#6abf45" stroke-width="1.8"/></svg>
</div>
<div class="abs langs">FRENCH &nbsp;|&nbsp; DUTCH &nbsp;|&nbsp; <span class="on">ENGLISH</span> &nbsp;|&nbsp; GERMAN &nbsp;|&nbsp; SPANISH</div>

<nav>
  <span class="abs nav-link on" style="left:199px">HOME</span>
  <span class="abs nav-link" style="left:259px">ACCOMADATION</span>
  <span class="abs nav-link" style="left:372px">RENT</span>
  <span class="abs nav-link" style="left:428px">CONTACT</span>
</nav>
<div class="abs brand head"><i></i>Harbor Nest Place</div>
<div class="abs account">
  <svg width="9" height="11" viewBox="0 0 9 11"><rect x="0" y="4.5" width="9" height="6.5" fill="#6abf45"/><path d="M2 4.5V3a2.5 2.5 0 0 1 5 0v1.5" fill="none" stroke="#6abf45" stroke-width="1.4"/></svg>
  <span>CREATE OR LOGIN &nbsp;|</span>
  <svg width="10" height="11" viewBox="0 0 10 11"><circle cx="5" cy="3" r="2.6" fill="#6abf45"/><path d="M0 11c0-3.5 2.2-5 5-5s5 1.5 5 5z" fill="#6abf45"/></svg>
  <span>MY ACCOUNT</span>
</div>

<div class="abs hero" role="img" aria-label="Blurred photo of a bright house front framed by trimmed green shrubs"></div>

<section class="abs panel rent">
  <h2>SEARCHING FOR ACCOMMODATION</h2>
  <div class="tile" style="left:11px">
    <svg viewBox="0 0 80 80" fill="none" stroke="#fff" stroke-width="2.2" stroke-linejoin="round">
      <rect x="12" y="14" width="34" height="56"/><rect x="46" y="30" width="22" height="40"/>
      <rect x="18" y="22" width="22" height="12"/><line x1="18" y1="42" x2="40" y2="42"/><line x1="18" y1="50" x2="40" y2="50"/><line x1="18" y1="58" x2="40" y2="58"/>
      <line x1="52" y1="38" x2="62" y2="38"/><line x1="52" y1="46" x2="62" y2="46"/><line x1="52" y1="54" x2="62" y2="54"/><line x1="6" y1="70" x2="74" y2="70"/>
    </svg>
  </div>
  <div class="tile" style="left:203px">
    <svg viewBox="0 0 80 80" fill="none" stroke="#fff" stroke-width="2.2">
      <circle cx="22" cy="30" r="7"/><circle cx="58" cy="30" r="7"/><circle cx="40" cy="26" r="9"/>
      <path d="M8 56c0-9 6-14 14-14 4 0 7 1 9 3"/><path d="M72 56c0-9-6-14-14-14-4 0-7 1-9 3"/><path d="M24 60c0-12 7-18 16-18s16 6 16 18z"/>
    </svg>
  </div>
  <div class="tile-label" style="left:11px">I Want To Rent A<br>Room Right Now !</div>
  <div class="tile-label" style="left:203px">I Want To<br>Join A Group</div>
</section>
<section class="abs panel owner">
  <h2>I HAVE A HOUSE FOR RENT</h2>
  <div class="tile" style="left:8px">
    <svg viewBox="0 0 80 80" fill="none" stroke="#fff" stroke-width="2.2" stroke-linejoin="round">
      <line x1="16" y1="8" x2="16" y2="74"/><line x1="16" y1="16" x2="66" y2="16"/><line x1="8" y1="74" x2="28" y2="74"/>
      <line x1="30" y1="16" x2="30" y2="24"/><line x1="58" y1="16" x2="58" y2="24"/>
      <rect x="24" y="24" width="42" height="32" rx="2"/><path d="M34 46v-8l8-6 8 6v8z"/><line x1="52" y1="62" x2="66" y2="62"/>
    </svg>
  </div>
  <div class="tile" style="left:202px">
    <svg viewBox="0 0 80 80" fill="none" stroke="#fff" stroke-width="2.2" stroke-linejoin="round">
      <rect x="10" y="18" width="32" height="54"/><line x1="10" y1="30" x2="42" y2="30"/><line x1="10" y1="42" x2="42" y2="42"/><line x1="10" y1="54" x2="42" y2="54"/>
      <line x1="21" y1="18" x2="21" y2="72"/><line x1="31" y1="18" x2="31" y2="72"/>
      <path d="M36 48l20-16 20 16"/><path d="M42 44v28h28V44"/><rect x="50" y="56" width="10" height="16"/><line x1="28" y1="8" x2="72" y2="30"/>
    </svg>
  </div>
  <div class="tile-label" style="left:8px">I Want to<br>Advetise !</div>
  <div class="tile-label" style="left:202px">Why Is Flatsharing<br>Interesting For Me ?</div>
</section>

<h2 class="abs sec-title" style="left:201px;top:778px">UNDER THE SPOTLIGHT</h2>
<h2 class="abs sec-title" style="left:611px;top:778px">UNDER THE SPOTLIGHT</h2>

<article class="abs card" style="left:201px;top:836px">
  <div class="photo" role="img" aria-label="Photo of a cheerful group of young people" style="background:linear-gradient(135deg,#c9a07a,#8a6a5a 50%,#4d6b8a)"></div>
  <div class="body"><h3>A NICE GROUP</h3>Young Workers,seeking for accomadatiom downtown<br><br>Average Age :35<br>Men and Women Welcome</div>
</article>
<article class="abs card" style="left:201px;top:1031px">
  <div class="photo" role="img" aria-label="Photo of young people celebrating together" style="background:linear-gradient(135deg,#2c2430,#7a4a50 50%,#c08868)"></div>
  <div class="body"><h3>ANOTHER NICE GROUP</h3>Young Ideas, Studying at university seeking for accomadation close to brussels University<br>Average Age :35<br>Men and Women Welcome</div>
</article>
<div class="abs btn" style="left:406px;top:1224px;width:185px">SEE MORE GROUPS</div>

<article class="abs card" style="left:611px;top:836px">
  <div class="photo" role="img" aria-label="Photo of a couple in front of a white modern house" style="background:linear-gradient(180deg,#c8d8ea,#e8ecee 45%,#9a9a90)"></div>
  <div class="body"><h3>HOUSE</h3>Town : &nbsp;New York<br><br>Rent Per Month : $250<br><br>Availability : 20</div>
</article>
<article class="abs card" style="left:611px;top:1031px">
  <div class="photo" role="img" aria-label="Photo of a suburban house with a green lawn" style="background:linear-gradient(180deg,#8fb0d8,#c9b98e 50%,#5f8a3a)"></div>
  <div class="body"><h3>APARTMENT</h3>Town : New York<br><br>Rent Per Month : $250<br><br>Availability : 20</div>
</article>
<div class="abs btn" style="left:817px;top:1224px;width:185px">SEE MORE HOUSES</div>

<div class="abs band"></div>
<h2 class="abs sp-title" style="left:201px;top:1386px">KEY SELLING POINTS FOR<br>THE ROOMATES</h2>
<h2 class="abs sp-title" style="left:611px;top:1386px">KEY SELLING POINTS FOR<br>THE OWNERS</h2>
<div class="abs sp-box" style="left:201px;top:1450px">At vero eos et accusamus et iusto odio dignissimos ducimus qui blanditiis praesentium voluptatum deleniti atque corrupti quos dolores et quas molestias excepturi sint occaecati cupiditate non provident, similique sunt in culpa qui officia deserunt mollitia animi, id est laborum et dolorum fuga. Et harum quidem rerum facilis est et expedita distinctio. Nam libero tempore, cum soluta nobis est eligendi optio cumque nihil impedit quo minus id quod maxime placeat facere possimus</div>
<div class="abs sp-box" style="left:611px;top:1450px">At vero eos et accusamus et iusto odio dignissimos ducimus qui blanditiis praesentium voluptatum deleniti atque corrupti quos dolores et quas molestias excepturi sint occaecati cupiditate non provident, similique sunt in culpa qui officia deserunt mollitia animi, id est laborum et dolorum fuga. Et harum quidem rerum facilis est et expedita distinctio. Nam libero tempore, cum soluta nobis est eligendi optio cumque nihil impedit quo minus id quod maxime placeat facere possimus</div>

<h2 class="abs faq-title">EVERYTHING YOU NEED TO KNOW<br>ABOUT FLAT SHARING</h2>

<div class="abs faq active" style="top:1862px;height:148px">
  <div class="num">1.</div>
  <p>At vero eos et accusamus et iusto odio dignissimos ducimus qui blanditiis praesentium voluptatum deleniti atque corrupti quos dolores et quas molestias excepturi sint occaecati cupiditate non provident, similique sunt in culpa qui officia deserunt mollitia animi, id est laborum et dolorum fuga. Et harum quidem rerum facilis est et expedita distinctio. Nam libero tempore, cum soluta nobis est eligendi optio cumque nihil impedit quo minus id quod maxime placeat facere possimus</p>
  <div class="more">MORE</div>
</div>
<div class="abs faq" style="top:2027px;height:152px">
  <div class="num">2.</div>
  <p>At vero eos et accusamus et iusto odio dignissimos ducimus qui blanditiis praesentium voluptatum deleniti atque corrupti quos dolores et quas molestias excepturi sint occaecati cupiditate non provident, similique sunt in culpa qui officia deserunt mollitia animi, id est laborum et dolorum fuga. Et harum quidem rerum facilis est et expedita distinctio. Nam libero tempore, cum soluta nobis est eligendi optio cumque nihil impedit quo minus id quod maxime placeat facere possimus</p>
  <div class="more">MORE</div>
</div>
<div class="abs faq" style="top:2193px;height:149px">
  <div class="num">3.</div>
  <p>At vero eos et accusamus et iusto odio dignissimos ducimus qui blanditiis praesentium voluptatum deleniti atque corrupti quos dolores et quas molestias excepturi sint occaecati cupiditate non provident, similique sunt in culpa qui officia deserunt mollitia animi, id est laborum et dolorum fuga. Et harum quidem rerum facilis est et expedita distinctio. Nam libero tempore, cum soluta nobis est eligendi optio cumque nihil impedit quo minus id quod maxime placeat facere possimus</p>
  <div class="more">MORE</div>
</div>
<div class="abs btn-teal">More Questions</div>

<div class="abs block green">PRE DEFINED SEARCHES</div>
<div class="abs block grey">TOOLS AND INFORMATION</div>

<footer class="abs footer">
  <div class="brand"><i></i>Harbor Nest Place</div>
  <div class="abs copy">© 2016 COMPANY NAME &nbsp;|&nbsp; ALL RIGHTS RESERVED</div>
</footer>

</body>
</html>
```